Marwick Jewelers New Website Design

This project is to provide a new design for an existing website. The existing website is marwickjewelers dot com . I have created a overview document that outlines all the details for the project. I do not need the design to be converted into HTML. I have a team for that already so please don't ask. I have a lot of images .. too many to upload here so they are on my dev server located at quillfoxstudio com slash marwick slash assets

Number of Pages Required

1 page

```html
<!DOCTYPE html>
<html lang="en">
<head>
<meta charset="utf-8">
<title>Marwick Jewelers</title>
<link href="https://fonts.googleapis.com/css2?family=Great+Vibes&family=Montserrat:wght@500;600;700&family=Nunito+Sans:wght@400;600&family=Open+Sans:wght@400&display=swap" rel="stylesheet">
<style>
:root{
  --teal:#5fe0ec;
  --teal-deep:#22b6c9;
  --ink:#111111;
  --muted:#7a7a7a;
  --navy:#0b1a33;
  --panel:#f4f4f4;
  --white:#ffffff;
  --black:#000000;
}
*{box-sizing:border-box;margin:0;padding:0}
html,body{width:1200px;height:3545px;overflow:hidden}
body{position:relative;background:var(--white);font-family:"Nunito Sans",sans-serif;color:var(--ink)}
.abs{position:absolute}
.script{font-family:"Great Vibes",cursive;color:var(--teal);font-size:30px;line-height:1}
.heading{font-family:"Montserrat",sans-serif;font-weight:600}
.btn{position:absolute;display:flex;align-items:center;justify-content:center;background:var(--teal);color:var(--white);font-family:"Montserrat",sans-serif;font-weight:600;border-radius:28px 28px 28px 4px}

/* nav */
.site-nav{position:absolute;left:0;top:0;width:1200px;height:85px;background:var(--white);z-index:3}
.nav-links{position:absolute;top:36px;left:397px;display:flex;gap:39px;font-family:"Open Sans",sans-serif;font-size:13px;text-transform:uppercase}
.nav-links .active{color:var(--teal)}
.logo-badge{position:absolute;left:128px;top:4px;width:170px;height:170px;border-radius:50%;background:var(--white);z-index:4;display:flex;align-items:center;justify-content:center;font-family:"Montserrat",sans-serif;font-weight:600;font-size:28px;color:#333}

/* hero */
.hero{position:absolute;left:0;top:85px;width:1200px;height:644px;background:radial-gradient(ellipse at 72% 45%,#34486a 0%,#142546 35%,#07112a 75%)}
.hero-title{left:110px;top:330px;font-size:56px;color:var(--white);font-weight:700}
.hero-text{left:112px;top:405px;width:460px;font-size:15px;line-height:26px;color:var(--white)}

/* about */
.about-text{left:476px;top:800px;width:612px;font-size:15px;line-height:25px;color:var(--muted)}
.photo{position:absolute;background:radial-gradient(ellipse at center,#3a3326 0%,#0b0b0b 70%)}

/* products */
.products{position:absolute;left:3px;top:1445px;width:1197px;height:653px;background:var(--panel);overflow:hidden}
.card{position:absolute;top:186px;width:296px;height:382px;transform:skewX(6deg);border-radius:46px 46px 0 46px;overflow:hidden}
.card-inner{position:absolute;inset:0;transform:skewX(-6deg)}
.card.dark{background:#0d0f1e}
.card.black{background:#050505}
.card.light{background:var(--white);box-shadow:0 6px 24px rgba(0,0,0,.08)}
.card-label{position:absolute;left:0;right:0;bottom:40px;text-align:center;color:var(--white);font-family:"Montserrat",sans-serif;font-weight:600;font-size:22px}
.card-photo{position:absolute;left:40px;right:40px;top:70px;height:190px;border-radius:50%;background:radial-gradient(ellipse at center,#7e7e8a 0%,rgba(30,30,40,0) 70%)}

/* testimonial */
.testimonial{position:absolute;left:0;top:2101px;width:1200px;height:431px;background:linear-gradient(120deg,#55d7e4 0%,#2bbacd 55%,#4fd4e2 100%)}
.review-card{position:absolute;left:177px;top:128px;width:850px;height:216px;background:var(--white)}
.review-photo{position:absolute;left:0;top:0;width:305px;height:216px;background:linear-gradient(135deg,#8a8f96,#3d3f44);clip-path:polygon(0 0,100% 0,77% 100%,0 100%)}
.round-btn{position:absolute;border-radius:50%;background:var(--white);display:flex;align-items:center;justify-content:center}

/* contact */
.field{position:absolute;background:var(--white);box-shadow:0 2px 14px rgba(0,0,0,.07);font-size:15px;color:#555;display:flex;align-items:flex-start;gap:8px;padding:22px 0 0 20px}

/* footer */
.footer{position:absolute;left:0;top:3177px;width:1200px;height:368px;background:var(--black);color:var(--white)}
.footer h4{position:absolute;font-family:"Montserrat",sans-serif;font-weight:600;font-size:23px}
.footer .item{position:absolute;font-size:15px;line-height:22px;display:flex;gap:10px}
.social{position:absolute;top:106px;width:30px;height:30px;border-radius:50%;background:var(--white)}
</style>
</head>
<body>

<header class="site-nav">
  <nav class="nav-links">
    <span class="active">Home</span><span>About Us</span><span>Contact Us</span><span>Jewelry Services and Repairs</span><span>Jewelry Education</span>
  </nav>
</header>
<div class="logo-badge">Marwick</div>

<section class="hero" role="img" aria-label="Silver ring with a pearl on a dark blue reflective surface"></section>
<div class="abs script" style="left:112px;top:290px">Welcome To</div>
<h1 class="abs heading hero-title">Marwick Jewelers</h1>
<p class="abs hero-text">Lorem ipsum dolor sit amet, consectetur adipiscing elit, sed do eiusmod tempor incididunt ut labore et</p>
<div class="btn" style="left:111px;top:480px;width:159px;height:58px;font-size:16px">Get Started</div>

<div class="abs script" style="left:112px;top:795px;font-size:26px">About Us</div>
<h2 class="abs heading" style="left:111px;top:830px;font-size:36px">Marwick Jewelers</h2>
<div class="btn" style="left:111px;top:903px;width:166px;height:53px;font-size:16px">Learn More</div>
<p class="abs about-text">Lorem ipsum dolor sit amet, consectetur adipiscing elit, sed do eiusmod tempor incididunt ut labore et dolore magna aliqua. Quis ipsum suspendisse ultrices gravida. Risus commodo viverra maecenas accumsan lacus vel facilisis. Lorem ipsum dolor sit amet, consectetur adipiscing elit, sed do eiusmod tempor incididunt ut labore et dolore magna aliqua. Quis ipsum suspendisse ultrices gravida. Risus commodo viverra maecenas accumsan lacus vel facilisis.</p>
<div class="photo" style="left:111px;top:991px;width:343px;height:329px;background:radial-gradient(ellipse at center,#3a3d5a 0%,#05060d 70%)" role="img" aria-label="Silver cuff bracelet set with blue stones"></div>
<div class="photo" style="left:473px;top:991px;width:613px;height:375px" role="img" aria-label="Thin gold bangle bracelet on black"></div>

<section class="products">
  <div class="abs script" style="left:0;width:1197px;text-align:center;top:72px;font-size:28px">Our Products</div>
  <h2 class="abs heading" style="left:0;width:1197px;text-align:center;top:100px;font-size:33px">Our Marwick Jewelers Products</h2>

  <div class="card black" style="left:-12px">
    <div class="card-inner">
      <div class="card-photo" role="img" aria-label="Diamond bracelet"></div>
      <div class="card-label">Diamond Brace</div>
    </div>
  </div>
  <div class="card light" style="left:288px">
    <div class="card-inner">
      <div class="abs" style="left:78px;top:27px;width:140px;height:104px;border-radius:50%;background:radial-gradient(ellipse at center,#f0c9a8 0%,rgba(255,255,255,0) 70%)" role="img" aria-label="Rose gold diamond ring"></div>
      <div class="abs heading" style="left:0;right:0;top:152px;text-align:center;font-size:22px">Diamond Rings</div>
      <div class="abs" style="left:128px;top:190px;width:40px;height:3px;background:var(--teal)"></div>
      <p class="abs" style="left:28px;right:22px;top:208px;text-align:center;font-size:15px;line-height:26px">Lorem ipsum dolor sit amet, consectetur adipiscing elit, sed do eiusmod tempor incididunt ut labore et dolore magna aliqua.</p>
      <div class="btn" style="left:92px;top:312px;width:148px;height:45px;font-size:16px">Contact Us</div>
    </div>
  </div>
  <div class="card dark" style="left:605px">
    <div class="card-inner">
      <div class="card-photo" role="img" aria-label="Purple gemstone ring" style="background:radial-gradient(ellipse at center,#8a4bb8 0%,rgba(20,20,40,0) 65%)"></div>
      <div class="card-label" style="bottom:52px">Gemstone Rings</div>
    </div>
  </div>
  <div class="card black" style="left:922px">
    <div class="card-inner">
      <div class="card-photo" role="img" aria-label="Pearl ring" style="background:radial-gradient(ellipse at center,#d9d2c4 0%,rgba(0,0,0,0) 60%)"></div>
      <div class="card-label" style="bottom:52px">Pearl Rings</div>
    </div>
  </div>
</section>

<section class="testimonial">
  <div class="abs script" style="left:0;width:1200px;text-align:center;top:36px;font-size:30px;color:var(--white)">Client Reviews</div>
  <h2 class="abs heading" style="left:0;width:1200px;text-align:center;top:64px;font-size:38px;color:var(--white)">Our Testimonial</h2>
  <div class="round-btn" style="left:162px;top:226px;width:27px;height:27px"><svg width="10" height="10" viewBox="0 0 10 10"><path d="M6.5 2 3.5 5l3 3" fill="none" stroke="#333" stroke-width="1.5"/></svg></div>
  <div class="round-btn" style="left:1011px;top:226px;width:27px;height:27px"><svg width="10" height="10" viewBox="0 0 10 10"><path d="M3.5 2l3 3-3 3" fill="none" stroke="#333" stroke-width="1.5"/></svg></div>
  <div class="review-card">
    <div class="review-photo" role="img" aria-label="Photo of the reviewing client"></div>
    <div class="round-btn" style="left:110px;top:92px;width:32px;height:32px"><svg width="12" height="12" viewBox="0 0 12 12"><path d="M3 1.5v9l7.5-4.5z" fill="#111"/></svg></div>
    <div class="abs heading" style="left:332px;top:28px;font-size:23px;font-weight:500">Lorem Ipsum</div>
    <p class="abs" style="left:332px;top:66px;width:490px;font-size:15px;line-height:25px;color:#444">Lorem ipsum dolor sit amet, consectetur adipiscing elit, sed do eiusmod tempor incididunt ut labore et dolore magna aliqua. Quis ipsum suspendisse ultrices gravida.</p>
    <div class="abs" style="left:333px;top:155px;width:38px;height:38px;border-radius:50%;background:linear-gradient(135deg,#6fd4de,#8a8f96)" role="img" aria-label="Client avatar"></div>
    <div class="abs heading" style="left:388px;top:155px;font-size:16px;font-weight:500">Rowan Ellery</div>
    <div class="abs" style="left:387px;top:176px;font-size:12px;color:var(--muted)">Lorem Ipsum</div>
  </div>
</section>

<div class="abs script" style="left:0;width:1200px;text-align:center;top:2612px;font-size:28px">Get A Quote</div>
<h2 class="abs heading" style="left:0;width:1200px;text-align:center;top:2638px;font-size:38px;font-weight:500">Contact Us</h2>
<p class="abs" style="left:300px;width:600px;text-align:center;top:2688px;font-size:15px;line-height:25px">Lorem ipsum dolor sit amet, consectetur adipiscing elit, sed do eiusmod tempor incididunt ut labore et dolore magna aliqua.</p>

<div class="field" style="left:110px;top:2766px;width:314px;height:49px;padding-top:15px"><svg width="14" height="14" viewBox="0 0 14 14"><circle cx="7" cy="4.5" r="3" fill="none" stroke="#555"/><path d="M1.5 13c0-3 2.5-5 5.5-5s5.5 2 5.5 5" fill="none" stroke="#555"/></svg>Name</div>
<div class="field" style="left:442px;top:2766px;width:313px;height:49px;padding-top:15px"><svg width="14" height="14" viewBox="0 0 14 14"><rect x="1" y="3" width="12" height="8" fill="none" stroke="#555"/><path d="M1 3l6 5 6-5" fill="none" stroke="#555"/></svg>Email</div>
<div class="field" style="left:773px;top:2766px;width:314px;height:49px;padding-top:15px"><svg width="14" height="14" viewBox="0 0 14 14"><path d="M3 1l2.5 3-1.5 1.5a8 8 0 0 0 4.5 4.5L10 8.5l3 2.5-1.5 2C6 13 1 8 1 2.5z" fill="none" stroke="#555"/></svg>Phone</div>
<div class="field" style="left:110px;top:2834px;width:977px;height:171px;padding-top:16px"><svg width="14" height="14" viewBox="0 0 14 14"><path d="M7 2C3.7 2 1 4 1 6.5c0 1.3.7 2.4 1.8 3.2L2 12.5l3-1.6c.6.2 1.3.2 2 .2 3.3 0 6-2 6-4.6S10.3 2 7 2z" fill="none" stroke="#555"/></svg>Message</div>
<div class="btn" style="left:521px;top:3049px;width:167px;height:50px;font-size:15px;font-family:'Nunito Sans',sans-serif">Send Message</div>

<footer class="footer">
  <div class="abs" style="left:129px;top:41px;width:198px;height:198px;border-radius:50%;background:var(--white);display:flex;align-items:center;justify-content:center;font-family:'Montserrat',sans-serif;font-weight:600;font-size:32px;color:#333">Marwick</div>
  <h4 style="left:417px;top:48px">Contact Us</h4>
  <div class="item" style="left:419px;top:91px"><svg width="11" height="14" viewBox="0 0 11 14" style="margin-top:4px"><path d="M5.5 0A5 5 0 0 0 .5 5c0 4 5 9 5 9s5-5 5-9a5 5 0 0 0-5-5z" fill="#fff"/><circle cx="5.5" cy="5" r="2" fill="#000"/></svg><span>Lorem ipsum dolor sit amet,<br>consectetur adipiscing elit</span></div>
  <div class="item" style="left:418px;top:151px"><svg width="13" height="13" viewBox="0 0 14 14" style="margin-top:4px"><path d="M3 1l2.5 3-1.5 1.5a8 8 0 0 0 4.5 4.5L10 8.5l3 2.5-1.5 2C6 13 1 8 1 2.5z" fill="#fff"/></svg>+1 555 014 2290</div>
  <div class="item" style="left:418px;top:187px"><svg width="14" height="12" viewBox="0 0 14 12" style="margin-top:5px"><rect x="0" y="1" width="14" height="10" fill="#fff"/><path d="M0 1l7 5 7-5" fill="none" stroke="#000"/></svg>info@marwickjewelers.com</div>
  <h4 style="left:714px;top:48px">Support</h4>
  <div class="item" style="left:717px;top:92px">Terms &amp; Conditions</div>
  <div class="item" style="left:717px;top:122px">Contact us</div>
  <div class="item" style="left:717px;top:153px">Privacy Policy</div>
  <h4 style="left:944px;top:48px">Follow Us</h4>
  <div class="social" style="left:944px"></div>
  <div class="social" style="left:984px"></div>
  <div class="social" style="left:1024px"></div>
  <div class="social" style="left:1062px"></div>
  <div class="abs" style="left:114px;top:267px;width:977px;height:1px;background:#333"></div>
  <div class="abs" style="left:0;width:1200px;top:300px;text-align:center;font-size:15px">©Copyrights 2022 <span style="color:var(--teal)">Marwick Jewelers</span> &nbsp;| &nbsp; All Rights Reserved</div>
</footer>

</body>
</html>
```